lantern pathway for children needs a website designer

We need a website designer for our new extension to our company known as 'lantern pathway' providing shadow support services to children based in Singapore. We are a sister branch of a private clinic 'Bright horizons' providing speech language, occupational, and educational therapy to children.

We would like to use our own photos. So the selected design should have a frame with pictures to give us an idea but we will replace them with our own. We will be needing help with inputting information and changing information throughout.

We would like to see designs that are simple, and professional. We have a logo (see attached). The result should convey professionalism in shadow support, fostering independent thinking and moving students towards self-learning.

Target Market(s)

Teachers, psychologists, parents

Industry/Entity Type

Clinic

Requirements
Should not have
• too distracting colours

```html
<!DOCTYPE html>
<html lang="en">
<head>
<meta charset="utf-8">
<title>Lantern Pathway — Shadow Support</title>
<link href="https://fonts.googleapis.com/css2?family=Open+Sans:wght@400;600;700&display=swap" rel="stylesheet">
<style>
:root{
  --red:#b3121a;
  --red-deep:#950000;
  --red-dark:#5a0000;
  --ink:#1e1e1e;
  --muted:#555;
  --grey-bg:#f1f1f1;
  --footer:#1c1c1c;
  --white:#fff;
}
*{margin:0;padding:0;box-sizing:border-box}
html,body{width:791px;height:1200px;overflow:hidden;background:var(--white)}
body{font-family:'Open Sans',sans-serif;color:var(--ink);position:relative}
.site-header{position:absolute;left:0;top:0;width:791px;height:77px;border-bottom:1px solid #e2e2e2}
.brand{position:absolute;left:44px;top:24px;display:flex;align-items:center;gap:8px;font-size:22px;font-weight:700;color:var(--red)}
.brand-mark{width:18px;height:18px;border-radius:50%;background:var(--red)}
.phone{position:absolute;right:55px;top:8px;display:flex;align-items:center;gap:5px;font-size:15px;color:var(--red)}
.main-nav{position:absolute;right:55px;top:43px;display:flex;font-size:10.5px;font-weight:600}
.main-nav a{color:var(--ink);text-decoration:none;padding:0 10px;border-left:1px solid #999;line-height:12px}
.main-nav a:first-child{border-left:0;color:var(--red)}
.main-nav a:last-child{padding-right:0}
.hero{position:absolute;left:0;top:77px;width:791px;height:317px;background:linear-gradient(90deg,#dfe6e6 0%,#d7c9a8 45%,#eac9a7 70%,#dbe6e8 100%)}
.hero-title{position:absolute;left:49px;top:105px;font-size:25px;font-weight:700;color:var(--red)}
.hero-sub{position:absolute;left:49px;top:140px;font-size:22px;color:var(--red)}
.hero-dots{position:absolute;left:367px;top:297px;display:flex;gap:3px}
.hero-dots span{width:12px;height:12px;border-radius:50%;background:var(--white)}
.hero-dots span:first-child{background:#000}
.about{position:absolute;left:0;top:394px;width:791px;height:189px;text-align:center}
.about h2{font-size:21px;font-weight:400;margin-top:20px;margin-bottom:3px}
.about p{font-size:8.6px;line-height:13.8px;color:var(--ink);padding:0 66px}
.about h3{font-size:12.5px;font-weight:400;margin-top:16px;margin-bottom:4px}
.services{position:absolute;left:0;top:583px;width:791px;height:314px;background:linear-gradient(180deg,var(--red-deep),var(--red-dark));color:var(--white);text-align:center}
.services h2{font-size:21px;font-weight:400;margin-top:20px}
.services .lead{font-size:10.5px;color:#e8a8a8}
.service{position:absolute;top:70px;width:210px;text-align:center}
.service .photo{width:152px;height:152px;margin:0 auto;border:1.5px dashed rgba(255,255,255,.6);border-radius:50%;padding:5px}
.service .photo div{width:100%;height:100%;border-radius:50%;border:4px solid var(--white)}
.service p{font-size:8.6px;line-height:13.8px;margin-top:12px;padding:0 4px}
.support{position:absolute;left:0;top:897px;width:791px;height:233px;background:var(--grey-bg)}
.support h2{text-align:center;font-size:21px;font-weight:400;margin-top:28px}
.support-col{position:absolute;top:78px;width:220px}
.support-col h3{font-size:13.5px;font-weight:400;color:var(--red-deep);line-height:14px;margin-bottom:5px}
.support-col p{font-size:8.4px;line-height:13.7px;color:var(--muted)}
.site-footer{position:absolute;left:0;top:1130px;width:791px;height:70px;background:var(--footer)}
.foot-nav{position:absolute;left:50px;top:16px;font-size:10px;font-weight:600;color:var(--white)}
.foot-nav span{margin:0 5px;font-weight:400}
.copy{position:absolute;left:50px;top:35px;font-size:8.5px;color:#888}
.social{position:absolute;right:46px;top:15px;display:flex;gap:5px}
.social span{width:15px;height:15px;border-radius:2px}
</style>
</head>
<body>
<header class="site-header">
  <div class="brand"><span class="brand-mark"></span>Lantern Pathway</div>
  <div class="phone">
    <svg width="14" height="14" viewBox="0 0 24 24" aria-hidden="true"><path fill="#999" d="M6.6 10.8a15 15 0 0 0 6.6 6.6l2.2-2.2c.3-.3.7-.4 1-.2 1.1.4 2.3.6 3.6.6.6 0 1 .4 1 1V20c0 .6-.4 1-1 1A17 17 0 0 1 3 4c0-.6.4-1 1-1h3.5c.6 0 1 .4 1 1 0 1.3.2 2.5.6 3.6.1.3 0 .7-.2 1z"/></svg>
    +65 6100 2480
  </div>
  <nav class="main-nav">
    <a href="#">HOME</a><a href="#">ABOUT US</a><a href="#">MISSION</a><a href="#">OUR SERVICES</a><a href="#">FOR SUPPORT</a><a href="#">REFERRERS</a>
  </nav>
</header>

<section class="hero" role="img" aria-label="Photo of a smiling mother and daughter touching foreheads">
  <div class="hero-title">Suspendisse vulputate aliquam</div>
  <div class="hero-sub">Vivamus sollicitudin metus</div>
  <div class="hero-dots"><span></span><span></span><span></span><span></span></div>
</section>

<section class="about">
  <h2>About Us Our Company</h2>
  <p>Lantern Pathway is part of the Brightwell Communication Group of Companies, who are providing speech language therapy, occupational therapy and educational therapy services to both the Singapore and the international school community.<br>Lantern Pathway aims to work in an integrated manner, respecting the work of the respective professionals involved and collaborating effectively</p>
  <h3>Our Mission</h3>
  <p>Lantern Pathway was borne out of our Speech language Pathologists’ frustration at a frequent lack of carry-over of goals to a classroom setting by external shadows.<br>Carrying over of goals in real settings is highly important as it allows for students to generalize skills quicker.</p>
</section>

<section class="services">
  <h2>Services We Provide</h2>
  <div class="lead">We provide a full fledged, seamless service that serves to:</div>
  <div class="service" style="left:56px">
    <div class="photo"><div role="img" aria-label="Photo of an elderly woman in a consultation" style="background:linear-gradient(135deg,#d9d4c8,#a9a08e)"></div></div>
    <p>Train shadows with a strong focus on equipping them with dynamic, clinical skills</p>
  </div>
  <div class="service" style="left:293px">
    <div class="photo"><div role="img" aria-label="Photo of a family with two children" style="background:linear-gradient(135deg,#c7d3e3,#8fa4c2)"></div></div>
    <p>Provide families with well-trained Shadows who are mentored by Speech Language Pathologists and Professional Therapists to carry out shadow support</p>
  </div>
  <div class="service" style="left:531px">
    <div class="photo"><div role="img" aria-label="Photo of a thoughtful woman" style="background:linear-gradient(135deg,#b8bfc6,#7f8a94)"></div></div>
    <p>Work with educational professionals (Educational Psychologists) to provide an effective solution to the learning needs of a student.</p>
  </div>
</section>

<section class="support">
  <h2>Shadow Support</h2>
  <div class="support-col" style="left:50px">
    <h3>What is shadow support</h3>
    <p>A shadow support is para-professional who can help a struggling student to integrate and learn in their school environment.<br>At different points in a student’s life, there may be a need for a para-professional who could step in to help make a differen</p>
  </div>
  <div class="support-col" style="left:287px">
    <h3>What are its Advantages?</h3>
    <p>A fully trained shadow support is an asset to the student who otherwise would have trouble fitting in and adapting to the mainstream school environment.</p>
    <p style="margin-top:3px">Additionally, working closely with the therapist at the centre would mean that the shadow is equipped with the skills necessary to not just adapt, but truly learn</p>
  </div>
  <div class="support-col" style="left:526px">
    <h3>How do I know if my child<br>needs shadowing</h3>
    <p>A consultation with our Speech Language Pathologist, along with an assessment by an Educational Psychologist would provide us with an indication of whether the child requires shadowing</p>
  </div>
</section>

<footer class="site-footer">
  <div class="foot-nav">HOME<span>|</span>ABOUT US<span>|</span>MISSION<span>|</span>OUR SERVICES<span>|</span>FOR SUPPORT<span>|</span>REFERRERS</div>
  <div class="copy">© 2014 Company Name.&nbsp; All right reserved.&nbsp; Term of Use</div>
  <div class="social" aria-label="Social links">
    <span style="background:#3b5998"></span><span style="background:#2fa9e0"></span><span style="background:#0e76a8"></span>
  </div>
</footer>
</body>
</html>
```